Computer consultant business card

Bexil Software is a newly started computer consulting company. It's a small one-man company that provides mostly Vornix applications but also websites in collaboration with designers. I'm running this company on the side of full time university studies.

I want the final design to be clean and memorable. Be creative! :)

Some inspiration:
http://www.pixelmarta.com/design/48317
http://www.pixelmarta.com/design/2739164/business-card-design-by-frostlynk
http://www.pixelmarta.com/design/604281/business-card-design-by-koralind-vestrabanu

See attachment for my company logo.
Updates

I would like to thank everyone for submitting! I'll need a couple of days to review and ultimately select a design.

Target Market(s)

Non-technical entrepreneurs and small companies.

Industry/Entity Type

University

Requirements
Must have
• My company logo.
In any way, both colors from my logo.
First- and last name, e-mail and phone number.
Double-sided design.
Nice to have
• Something creative with the symbol in my logo

```html
<!DOCTYPE html>
<html lang="en">
<head>
<meta charset="utf-8">
<title>Bexil Software — Business Card</title>
<link rel="stylesheet" href="https://fonts.googleapis.com/css2?family=Open+Sans:wght@400;600;700&display=swap">
<style>
  :root {
    --stage: #1d1d1f;
    --brand-blue: #3f67ad;
    --brand-blue-deep: #2f5699;
    --brand-blue-light: #4a74bb;
    --ink: #2b2b2d;
    --paper: #ffffff;
    --ghost: #efeff1;
    --muted: #3a3a3c;
  }
  * { margin: 0; padding: 0; box-sizing: border-box; }
  html, body {
    width: 1200px; height: 900px; overflow: hidden;
    background: var(--stage);
    font-family: "Open Sans", Arial, sans-serif;
  }
  .sheet {
    width: 1200px; height: 900px;
    display: flex; flex-direction: column;
    align-items: center; justify-content: center; gap: 56px;
  }
  .card {
    position: relative;
    width: 640px; height: 366px;
    border-radius: 28px;
    overflow: hidden;
  }
  .card-art { position: absolute; inset: 0; width: 100%; height: 100%; }

  /* Back side */
  .card--back {
    background: radial-gradient(ellipse 70% 90% at 55% 45%, var(--brand-blue-light) 0%, var(--brand-blue) 55%, var(--brand-blue-deep) 100%);
  }
  .wordmark {
    position: absolute;
    display: flex; align-items: center; gap: 18px;
    font-weight: 600; letter-spacing: 1px; line-height: 1;
    white-space: nowrap;
  }
  .wordmark__dot { border-radius: 50%; flex: none; }
  .card--back .wordmark {
    left: 50%; top: 50%; transform: translate(-50%, -50%);
    color: var(--paper); font-size: 92px;
  }
  .card--back .wordmark__dot { width: 70px; height: 70px; background: var(--paper); }

  /* Front side */
  .card--front { background: var(--paper); }
  .card--front .wordmark {
    left: 386px; top: 126px;
    gap: 14px;
    color: var(--ink); font-size: 58px;
  }
  .card--front .wordmark__dot { width: 44px; height: 44px; background: var(--brand-blue); }

  .holder {
    position: absolute; left: 34px; top: 222px;
    color: var(--paper);
    white-space: nowrap;
  }
  .holder__name { font-weight: 700; font-size: 26px; letter-spacing: 0.5px; line-height: 1.15; }
  .holder__title { font-weight: 400; font-size: 21px; line-height: 1.2; }

  .contact {
    position: absolute; right: 24px; bottom: 22px;
    display: flex; gap: 18px;
    font-size: 14px; color: var(--muted);
    white-space: nowrap;
  }
  .contact__item { display: flex; align-items: center; gap: 7px; }
  .contact__icon { width: 20px; height: 20px; flex: none; }
</style>
</head>
<body>
<main class="sheet">

  <section class="card card--back" aria-label="Card back">
    <div class="wordmark">
      <span class="wordmark__dot"></span>
      <span class="wordmark__text">bexil</span>
    </div>
  </section>

  <section class="card card--front" aria-label="Card front">
    <svg class="card-art" viewBox="0 0 640 366" aria-hidden="true">
      <circle cx="604" cy="118" r="90" fill="var(--ghost)"/>
      <path d="M0,0 L600,0 Q300,80 230,366 L0,366 Z" fill="var(--brand-blue)"/>
      <path d="M614,-4 Q314,84 246,370" fill="none" stroke="var(--ink)" stroke-width="10"/>
    </svg>

    <div class="wordmark">
      <span class="wordmark__dot"></span>
      <span class="wordmark__text">bexil</span>
    </div>

    <div class="holder">
      <p class="holder__name">YOUR NAME</p>
      <p class="holder__title">Job Title</p>
    </div>

    <div class="contact">
      <p class="contact__item">
        <svg class="contact__icon" viewBox="0 0 22 22" aria-hidden="true">
          <circle cx="11" cy="11" r="9.5" fill="none" stroke="var(--brand-blue)" stroke-width="2"/>
          <rect x="8" y="5.5" width="6" height="11" rx="1.2" fill="none" stroke="var(--brand-blue)" stroke-width="1.4"/>
        </svg>
        <span>000-000-000</span>
      </p>
      <p class="contact__item">
        <svg class="contact__icon" viewBox="0 0 22 22" aria-hidden="true">
          <circle cx="11" cy="11" r="9.5" fill="none" stroke="var(--brand-blue)" stroke-width="2"/>
          <rect x="6" y="7.5" width="10" height="7" fill="none" stroke="var(--brand-blue)" stroke-width="1.4"/>
          <path d="M6,7.5 L11,11.5 L16,7.5" fill="none" stroke="var(--brand-blue)" stroke-width="1.4"/>
        </svg>
        <span>name@domainname.com</span>
      </p>
    </div>
  </section>

</main>
</body>
</html>
```